Newspaper ad for web design services

I have a paid space in a local newspaper size: 4.5085" W x 2.6875" H.
I want to use it for promoting my web design services.
Designers have the freedom to design the ad and the offer.
The goal is to have people contact me for business web design.
I published one ad last month and it totally failed to bring any attention.
Feel free to change or add anything you think can be more effective to attract potential customers (I can create any tripwire you consider will work)
Target: Houston-based business owners looking to get a new website or to update their existing one.

```html
<!DOCTYPE html>
<html lang="en">
<head>
<meta charset="utf-8">
<title>Norva Designs – Newspaper Ad</title>
<link href="https://fonts.googleapis.com/css2?family=Montserrat:wght@500;600;700;800&display=swap" rel="stylesheet">
<style>
  :root {
    --brand-blue: #3d62ad;
    --ink: #1e1e1e;
    --icon-grey: #5d5d5d;
    --sky-top: #bfd6e6;
    --sky-mid: #e4eef5;
    --paper: #ffffff;
    --frame: #2a2a2a;
    --button-top: #6a6a6a;
    --button-bottom: #232323;
  }
  html, body {
    margin: 0;
    padding: 0;
    overflow: hidden;
    background: var(--paper);
  }
  .ad {
    position: relative;
    width: 1200px;
    height: 718px;
    box-sizing: border-box;
    border: 1.5px solid var(--frame);
    overflow: hidden;
    font-family: "Montserrat", Arial, sans-serif;
    background: linear-gradient(180deg, var(--sky-top) 0%, var(--sky-mid) 35%, var(--paper) 62%);
  }
  .brand {
    position: absolute;
    left: 53px;
    top: 40px;
    display: flex;
    align-items: center;
    gap: 14px;
  }
  .brand-mark {
    width: 66px;
    height: 66px;
    background: var(--brand-blue);
  }
  .brand-name {
    margin: 0;
    font-weight: 500;
    font-size: 35px;
    line-height: 1;
    color: var(--ink);
    letter-spacing: -0.5px;
  }
  .headline {
    position: absolute;
    left: 53px;
    top: 152px;
    margin: 0;
    font-weight: 700;
    font-size: 39px;
    line-height: 1.09;
    color: var(--ink);
    letter-spacing: -0.3px;
  }
  .headline .promise {
    display: block;
    margin-top: 6px;
    font-weight: 800;
    font-size: 47px;
    line-height: 1.06;
    color: var(--brand-blue);
  }
  .showcase {
    position: absolute;
    left: 608px;
    top: 18px;
    width: 592px;
    height: 390px;
    background: radial-gradient(ellipse at 60% 45%, #5c6f82 0%, #9fb3c4 45%, rgba(220,232,241,0) 75%);
  }
  .benefits-band {
    position: absolute;
    left: 0;
    top: 450px;
    width: 100%;
    height: 154px;
    background: var(--brand-blue);
  }
  .benefit {
    position: absolute;
    top: 390px;
    width: 280px;
    margin-left: -140px;
    text-align: center;
  }
  .benefit-icon {
    display: block;
    width: 120px;
    height: 120px;
    margin: 0 auto;
  }
  .benefit-label {
    margin: 16px 0 0;
    font-weight: 800;
    font-size: 30px;
    line-height: 1.05;
    color: var(--paper);
  }
  .divider {
    position: absolute;
    top: 519px;
    width: 3px;
    height: 64px;
    background: var(--paper);
  }
  .cta-button {
    position: absolute;
    left: 62px;
    top: 622px;
    width: 260px;
    height: 75px;
    border-radius: 38px;
    background: linear-gradient(180deg, var(--button-top), var(--button-bottom));
    color: var(--paper);
    font-weight: 500;
    font-size: 26px;
    line-height: 1.1;
    text-align: center;
    display: flex;
    align-items: center;
    justify-content: center;
  }
  .cta-url {
    position: absolute;
    left: 358px;
    top: 632px;
    margin: 0;
    font-weight: 700;
    font-size: 39px;
    color: var(--brand-blue);
    letter-spacing: -0.2px;
  }
</style>
</head>
<body>
<main class="ad">
  <div class="brand">
    <div class="brand-mark"></div>
    <p class="brand-name">Norva<br>Designs</p>
  </div>

  <h1 class="headline">The ONE easy<br>change will make your
    <span class="promise">BUSINESS WEBISTE<br>DOUBLE YOUR SALES</span>
  </h1>

  <div class="showcase" role="img" aria-label="Desktop monitor with several sample website layouts floating in front of it"></div>

  <div class="benefits-band"></div>

  <div class="benefit" style="left:187px">
    <svg class="benefit-icon" viewBox="0 0 120 120" aria-hidden="true">
      <circle cx="60" cy="60" r="58" fill="var(--icon-grey)" stroke="#fff" stroke-width="3"/>
      <g fill="none" stroke="#fff" stroke-width="2.5" stroke-linecap="round">
        <circle cx="46" cy="36" r="6"/><circle cx="60" cy="33" r="7"/><circle cx="74" cy="36" r="6"/>
        <path d="M36 58v-6a10 10 0 0 1 10-10M84 58v-6a10 10 0 0 0-10-10M48 58v-6a12 12 0 0 1 24 0v6"/>
        <path d="M28 80h16l14 6h14a5 5 0 0 0 0-10H60l24-8a5 5 0 0 1 4 8L66 92H44l-16-4"/>
      </g>
    </svg>
    <p class="benefit-label">GET MORE NEW<br>CUSTOMERS</p>
  </div>
  <div class="divider" style="left:359px"></div>

  <div class="benefit" style="left:494px">
    <svg class="benefit-icon" viewBox="0 0 120 120" aria-hidden="true">
      <circle cx="60" cy="60" r="58" fill="var(--icon-grey)" stroke="#fff" stroke-width="3"/>
      <g fill="none" stroke="#fff" stroke-width="2.5" stroke-linejoin="round">
        <path d="M34 44l40-12 4 10"/>
        <rect x="30" y="42" width="58" height="44" rx="7"/>
        <rect x="36" y="48" width="46" height="32" rx="4" stroke-dasharray="4 3"/>
        <rect x="76" y="56" width="16" height="14" rx="4"/>
        <circle cx="84" cy="63" r="2"/>
      </g>
    </svg>
    <p class="benefit-label">BUY MORE</p>
  </div>
  <div class="divider" style="left:624px"></div>

  <div class="benefit" style="left:760px">
    <svg class="benefit-icon" viewBox="0 0 120 120" aria-hidden="true">
      <circle cx="60" cy="60" r="58" fill="var(--icon-grey)" stroke="#fff" stroke-width="3"/>
      <g fill="none" stroke="#fff" stroke-width="2.2" stroke-linejoin="round">
        <path d="M50 24l3 6 6 1-4.5 4 1 6-5.5-3-5.5 3 1-6-4.5-4 6-1z"/>
        <path d="M70 24l3 6 6 1-4.5 4 1 6-5.5-3-5.5 3 1-6-4.5-4 6-1z"/>
        <path d="M40 44l3 6 6 1-4.5 4 1 6-5.5-3-5.5 3 1-6-4.5-4 6-1z"/>
        <path d="M60 44l3 6 6 1-4.5 4 1 6-5.5-3-5.5 3 1-6-4.5-4 6-1z"/>
        <path d="M80 44l3 6 6 1-4.5 4 1 6-5.5-3-5.5 3 1-6-4.5-4 6-1z"/>
        <path d="M30 84h14l12 5h14a4 4 0 0 0 0-8H58l22-7a4 4 0 0 1 4 7L64 94H44l-14-4" stroke-linecap="round"/>
      </g>
    </svg>
    <p class="benefit-label">GET MORE<br>REVIEWS</p>
  </div>
  <div class="divider" style="left:886px"></div>

  <div class="benefit" style="left:1045px">
    <svg class="benefit-icon" viewBox="0 0 120 120" aria-hidden="true">
      <circle cx="60" cy="60" r="58" fill="var(--icon-grey)" stroke="#fff" stroke-width="3"/>
      <g fill="none" stroke="#fff" stroke-width="2.5" stroke-linejoin="round" stroke-linecap="round">
        <path d="M30 52h10l30-18v50L40 68H30z"/>
        <path d="M38 68l6 18h8l-4-16"/>
        <path d="M80 50l10-6M80 60h12M80 70l10 6M74 38l4-8"/>
      </g>
    </svg>
    <p class="benefit-label">REFER MORE<br>CUSTOMERS</p>
  </div>

  <div class="cta-button">Download the<br>FREE eBook</div>
  <p class="cta-url">Visit : norva-designs.com/website</p>
</main>
</body>
</html>
```